Manufacturer's Representative Group needs a clean new Website

We represent and sell a number of suppliers that design and build products used in Biopharmaceutical manufacturing. Our sales region is in the central US. Our customer base is scientific / engineering based - so clean, we organized design with a focus on the products - easy and clear navigation is necessary. We do not sell direct or warehouse product - so e-commerce is not needed. Our customers will use the website for reference on what we do and offer - we will use the site as a platform to present products from each vendor and the home page will be used to capture an overview and draw users deeper into the site. You can view our current site - which needs A LOT of help to get ideas on products represented and types of products

Target Market(s)

Engineers and Pharmaceutical / Bio pharm end users

Industry/Entity Type

E-Commerce

Number of Pages Required

2 page

Font styles to use
Sans Serif

Requirements
Must have
• I need a home page that provides a snapshot of my company and the product lines we represent - then a second page that I can copy as a template for each line I rep as well as for an "About us / contact" page.
• I would like to be able to manage content on the pages so something easy to adjust pictures or add content is a must
• Must use our logo

```html
<!DOCTYPE html>
<html lang="en">
<head>
<meta charset="utf-8">
<title>Northfield Bio — Home</title>
<link href="https://fonts.googleapis.com/css2?family=Open+Sans:wght@400;600&family=Ubuntu:wght@400;500;700&display=swap" rel="stylesheet">
<style>
:root{
  --orange:#f07a1f;
  --navy:#1b2a5c;
  --text:#6f6f6f;
  --muted:#9a9a9a;
  --line:#d8d8d8;
  --band:#eeebe5;
  --footer:#7b7b7b;
  --white:#ffffff;
}
*{margin:0;padding:0;box-sizing:border-box}
html,body{width:843px;height:1200px;overflow:hidden;background:var(--white)}
body{position:relative;font-family:"Open Sans",sans-serif;color:var(--text)}
.site-header{position:absolute;left:0;top:0;width:843px;height:80px;border-top:2px solid var(--orange);background:var(--white)}
.brand{position:absolute;left:69px;top:24px;display:flex;align-items:center;gap:8px;font-family:"Ubuntu",sans-serif;font-weight:500;font-size:22px;color:var(--navy)}
.brand-dot{width:16px;height:16px;border-radius:50%;background:var(--orange)}
.main-nav a{position:absolute;top:35px;font-size:8.5px;color:#555;text-decoration:none;letter-spacing:.2px}
.main-nav a.active{color:var(--orange);font-weight:600}
.hero{position:absolute;left:0;top:80px;width:843px;height:314px;background:linear-gradient(90deg,#3a4a4c 0%,#8f9394 35%,#c9c4bc 60%,#d9a870 100%)}
.hero-photo{position:absolute;inset:0;background:radial-gradient(ellipse at 30% 75%,rgba(30,160,150,.55),transparent 45%),radial-gradient(ellipse at 60% 40%,rgba(240,240,240,.5),transparent 55%)}
.hero-title{position:absolute;left:0;width:843px;top:122px;text-align:center;font-family:"Ubuntu",sans-serif;font-weight:500;font-size:26px;line-height:41px;color:var(--white);text-transform:uppercase}
.hero-dots{position:absolute;top:210px;left:405px;display:flex;gap:4px}
.hero-dots span{width:8px;height:8px;border-radius:50%;background:var(--orange)}
.hero-dots span.on{background:var(--white)}
.hero-shadow{position:absolute;left:10px;top:394px;width:823px;height:8px;background:radial-gradient(ellipse at 50% 0,rgba(0,0,0,.25),transparent 70%)}
.section-title{position:absolute;left:0;width:843px;text-align:center;font-family:"Ubuntu",sans-serif;font-weight:500;font-size:14.5px;color:var(--navy)}
.divider{position:absolute;left:376px;width:91px;height:10px}
.lead{position:absolute;left:60px;width:723px;text-align:center;font-size:7.4px;line-height:14.4px;color:var(--text)}
.btn-more{position:absolute;left:386px;top:525px;width:71px;height:25px;border:1px solid #c8c8c8;border-radius:2px;font-size:8px;color:#666;display:flex;align-items:center;justify-content:center}
.carousel-arrows{position:absolute;left:747px;top:578px;display:flex;gap:3px}
.carousel-arrows span{width:11px;height:11px;border-radius:50%;background:#888}
.product-card{position:absolute;top:662px;width:209px;height:130px;border:1px solid #e6e6e6;background:var(--white);padding:6px}
.product-card::after{content:"";position:absolute;left:10px;right:10px;bottom:-10px;height:8px;background:radial-gradient(ellipse at 50% 0,rgba(0,0,0,.22),transparent 70%)}
.product-image{width:100%;height:100%}
.partner{position:absolute;top:892px;width:110px;height:50px;background:var(--white);box-shadow:0 0 4px rgba(0,0,0,.12);display:flex;align-items:center;justify-content:center;font-family:"Open Sans",sans-serif;font-weight:600;font-size:10px;color:var(--navy);gap:5px;white-space:nowrap}
.partner-mark{width:9px;height:9px;border-radius:50%;background:var(--navy)}
.testimonials{position:absolute;left:0;top:972px;width:843px;height:168px;background:var(--band)}
.testimonials-title{position:absolute;left:0;width:843px;top:22px;text-align:center;font-family:"Ubuntu",sans-serif;font-weight:400;font-size:13px;color:#555}
.testimonials-title b{font-weight:500;color:#333}
.round-arrow{position:absolute;top:20px;width:19px;height:19px}
.quote-text{position:absolute;left:240px;width:363px;top:68px;text-align:center;font-size:7.4px;line-height:14.4px;color:#555}
.quote-author{position:absolute;left:0;width:843px;top:108px;text-align:center;font-size:8px;font-weight:600;color:#444}
.site-footer{position:absolute;left:0;top:1140px;width:843px;height:60px;background:var(--footer);color:var(--white)}
.footer-nav{position:absolute;left:70px;top:12px;font-size:7.5px}
.footer-nav span{margin:0 4px}
.copyright{position:absolute;left:70px;top:34px;font-size:6.4px}
.social{position:absolute;left:683px;top:20px;display:flex;gap:4px}
.social span{width:19px;height:19px;border-radius:50%;background:#959595;border:1px solid #8a8a8a}
</style>
</head>
<body>
<header class="site-header">
  <div class="brand"><span class="brand-dot"></span>Northfield Bio</div>
  <nav class="main-nav">
    <a class="active" style="left:416px">HOME</a>
    <a style="left:476px">ABOUT US</a>
    <a style="left:549px">OUR PRODUCT</a>
    <a style="left:645px">OVERVIEW</a>
    <a style="left:722px">CONTACT US</a>
  </nav>
</header>

<section class="hero">
  <div class="hero-photo" role="img" aria-label="Lab technician in a clean suit and teal gloves handling a pipette and glass bottle"></div>
  <h1 class="hero-title">New from&nbsp; - Certified Clean<br>Purevessels</h1>
  <div class="hero-dots"><span></span><span></span><span class="on"></span></div>
</section>
<div class="hero-shadow"></div>

<h2 class="section-title" style="top:419px">ABOUT US</h2>
<svg class="divider" style="top:445px" viewBox="0 0 91 10"><line x1="0" y1="5" x2="37" y2="5" stroke="#d0d0d0"/><line x1="54" y1="5" x2="91" y2="5" stroke="#d0d0d0"/><circle cx="45.5" cy="5" r="2.5" fill="#999"/></svg>
<p class="lead" style="top:467px">Northfield Biosolutions is a distribution channel, licensed partner and manufacturers representative group providing high quality fluid handling products and technical services to the Midwestern<br>biopharmaceutical community. With a core staff of experienced professionals and a team approach to all customer needs, we offer over 30 years of cGMP experience in<br>the selection and use of most process consumable products. We're looking forward to working with you!</p>
<div class="btn-more">READ MORE</div>

<h2 class="section-title" style="top:575px">OUR PRODUCT</h2>
<div class="carousel-arrows"><span></span><span></span></div>
<svg class="divider" style="top:601px" viewBox="0 0 91 10"><line x1="0" y1="5" x2="37" y2="5" stroke="#d0d0d0"/><line x1="54" y1="5" x2="91" y2="5" stroke="#d0d0d0"/><circle cx="45.5" cy="5" r="2.5" fill="#999"/></svg>
<p class="lead" style="top:627px">We are proud to announce that we now represent the Veritas Solutions array of Reactors, Controllers, Sensors and Service</p>

<div class="product-card" style="left:70px"><div class="product-image" role="img" aria-label="Single-use bag containers and stainless steel transport cart" style="background:linear-gradient(180deg,#d6e8f2,#eef5f8)"></div></div>
<div class="product-card" style="left:317px"><div class="product-image" role="img" aria-label="Assorted clear silicone fittings, caps and tubing on a blue backdrop" style="background:radial-gradient(ellipse at 50% 40%,#5b7fa6,#1d2f55)"></div></div>
<div class="product-card" style="left:564px"><div class="product-image" role="img" aria-label="Coiled translucent process tubing on a blue backdrop" style="background:radial-gradient(ellipse at 50% 50%,#3f6fb8,#0f2250)"></div></div>

<h2 class="section-title" style="top:839px">COMPANIES REPRESENTED</h2>
<svg class="divider" style="top:865px" viewBox="0 0 91 10"><line x1="0" y1="5" x2="37" y2="5" stroke="#d0d0d0"/><line x1="54" y1="5" x2="91" y2="5" stroke="#d0d0d0"/><circle cx="45.5" cy="5" r="2.5" fill="#999"/></svg>

<div class="partner" style="left:69px"><span class="partner-mark"></span>CleanFlow</div>
<div class="partner" style="left:188px">Hartline Polymers</div>
<div class="partner" style="left:307px">Brandt Pumps</div>
<div class="partner" style="left:425px">Veritas</div>
<div class="partner" style="left:544px">Flexline Tubing Co.</div>
<div class="partner" style="left:663px"><span class="partner-mark"></span>Modula Rooms</div>

<section class="testimonials">
  <svg class="round-arrow" style="left:348px" viewBox="0 0 19 19"><circle cx="9.5" cy="9.5" r="8.5" fill="none" stroke="#999"/><path d="M11 6 L7.5 9.5 L11 13" fill="none" stroke="#888" stroke-width="1.4"/></svg>
  <h2 class="testimonials-title">Others <b>about us</b></h2>
  <svg class="round-arrow" style="left:478px" viewBox="0 0 19 19"><circle cx="9.5" cy="9.5" r="8.5" fill="none" stroke="#999"/><path d="M8 6 L11.5 9.5 L8 13" fill="none" stroke="#888" stroke-width="1.4"/></svg>
  <svg class="divider" style="top:47px" viewBox="0 0 91 10"><line x1="0" y1="5" x2="37" y2="5" stroke="#cfcbc3"/><line x1="54" y1="5" x2="91" y2="5" stroke="#cfcbc3"/><circle cx="45.5" cy="5" r="2.5" fill="#999"/></svg>
  <p class="quote-text">Meeting USP 788 Particulate Matter in Injections, and the equivalent EP and JP quality standards. We<br>offer these in standard and custom configurations!</p>
  <p class="quote-author">Alan Reed Moore, Process Engineer</p>
</section>

<footer class="site-footer">
  <div class="footer-nav">HOME<span>/</span>ABOUT US<span>/</span>OUR PRODUCT<span>/</span>OVERVIEW<span>/</span>CONTACT US</div>
  <div class="copyright">© NORTHFIELD BIOSOLUTIONS, CORP</div>
  <div class="social"><span></span><span></span><span></span><span></span></div>
</footer>
</body>
</html>
```